Employee Benefits and Insurance Consulting

We are an existing company with over 30 years experience but are changing our name. We would like a simple design with grey tones.

Industry/Entity Type

Insurance

Contact Information for Business Card

Marlow Benefits Consulting
Gerald P Hollins CEO
5172 Brackenridge Road
Cedar Bluff, TN 37919
gerald@marlowbenefits-example.com
865-412-5593 - O
865-247-3861 - C

```html
<!DOCTYPE html>
<html lang="en">
<head>
<meta charset="utf-8">
<title>Marlow Benefits Consulting – Business Card</title>
<link href="https://fonts.googleapis.com/css2?family=Open+Sans:wght@400;600;700&display=swap" rel="stylesheet">
<style>
  :root {
    --backdrop: #1a1a1a;
    --card-white: #ffffff;
    --brand-red: #d21414;
    --brand-red-deep: #b80f0f;
    --ink: #1e1e1e;
    --ink-soft: #3a3a3a;
    --rule-grey: #b5b5b5;
  }
  * { margin: 0; padding: 0; box-sizing: border-box; }
  html, body {
    width: 1200px; height: 900px; overflow: hidden;
    background: var(--backdrop);
    font-family: "Open Sans", Arial, sans-serif;
  }
  .stage { position: relative; width: 1200px; height: 900px; }
  .card { position: absolute; top: 170px; width: 347px; height: 561px; }
  .card--front { left: 259px; background: var(--card-white); }
  .card--back { left: 631px; background: var(--brand-red); }

  .tab { position: absolute; left: 102px; width: 143px; background: var(--brand-red); }
  .tab--top { top: 0; height: 30px; }
  .tab--bottom { bottom: 0; height: 28px; }

  .company-name {
    position: absolute; top: 166px; left: 0; width: 100%;
    text-align: center; color: var(--brand-red);
    font-weight: 700; font-size: 35px; line-height: 48px;
    letter-spacing: -0.3px;
  }
  .company-tagline {
    position: absolute; top: 214px; left: 28px; right: 28px;
    display: flex; align-items: center; gap: 8px;
    color: var(--ink-soft); font-size: 13px; letter-spacing: 2.5px;
    line-height: 18px;
  }
  .company-tagline::before, .company-tagline::after {
    content: ""; flex: 1; height: 1px; background: var(--rule-grey);
  }
  .person {
    position: absolute; top: 284px; left: 0; width: 100%;
    text-align: center; color: var(--brand-red);
    font-weight: 600; font-size: 19px;
  }
  .person .role { font-size: 14px; }
  .contacts {
    position: absolute; top: 357px; left: 0; width: 100%;
    list-style: none; text-align: center;
    color: var(--ink); font-size: 14.5px; line-height: 23px;
  }
  .contacts svg {
    width: 11px; height: 11px; fill: var(--brand-red);
    vertical-align: -1px; margin-right: 6px;
  }
  .address {
    position: absolute; top: 456px; left: 0; width: 100%;
    text-align: center; color: var(--ink);
    font-size: 14.5px; line-height: 21px; font-style: normal;
  }
  .back-name {
    position: absolute; top: 230px; left: 0; width: 100%;
    text-align: center; color: var(--brand-red-deep);
    font-weight: 700; font-size: 40px; line-height: 1.1;
  }
</style>
</head>
<body>
<main class="stage">
  <section class="card card--front">
    <div class="tab tab--top"></div>
    <h1 class="company-name">Marlow Benefits</h1>
    <p class="company-tagline">CONSULTING</p>
    <p class="person">Gerald P Hollins - <span class="role">CEO</span></p>
    <ul class="contacts">
      <li><svg viewBox="0 0 24 24" aria-hidden="true"><path d="M6.6 10.8a15.1 15.1 0 0 0 6.6 6.6l2.2-2.2a1 1 0 0 1 1-.25 11.4 11.4 0 0 0 3.6.57 1 1 0 0 1 1 1V20a1 1 0 0 1-1 1A17 17 0 0 1 3 4a1 1 0 0 1 1-1h3.5a1 1 0 0 1 1 1c0 1.25.2 2.45.57 3.57a1 1 0 0 1-.25 1z"/></svg>865-247-3861</li>
      <li><svg viewBox="0 0 24 24" aria-hidden="true"><path d="M7 1h10a2 2 0 0 1 2 2v18a2 2 0 0 1-2 2H7a2 2 0 0 1-2-2V3a2 2 0 0 1 2-2zm0 3v14h10V4zm5 15.5a1.2 1.2 0 1 0 0 2.4 1.2 1.2 0 0 0 0-2.4z"/></svg>865-412-5593</li>
      <li><svg viewBox="0 0 24 24" aria-hidden="true"><path d="M2 5h20v14H2zm2 2v.5l8 5 8-5V7zm0 2.9V17h16V9.9l-8 5z"/></svg>gerald@marlowbenefits-example.com</li>
    </ul>
    <address class="address">5172 Brackenridge Road<br>Cedar Bluff, TN 37919</address>
    <div class="tab tab--bottom"></div>
  </section>
  <section class="card card--back">
    <p class="back-name">Marlow Benefits<br>Consulting</p>
  </section>
</main>
</body>
</html>
```